We are a recruitment company based in Norwich/Cambridge England.
I have included our company logo which we want to remain the same.

What we are looking for is a new creative Business card which will really stand out!!

Contact Information for Business Card

Harriet Dunmore
email: Harriet@plavex.co.uk
Address: Brackwell House
Fenmoor Enterprise Park
Partridge Way
Norwich
QB9 3KX
Tel:01632 960418

```html
<!DOCTYPE html>
<html lang="en">
<head>
<meta charset="utf-8">
<title>Plavex business card</title>
<link rel="stylesheet" href="https://fonts.googleapis.com/css2?family=Open+Sans:wght@300;400;600&display=swap">
<style>
  :root {
    --bg: #e9e7e3;
    --green: #7dc242;
    --green-dark: #6cb233;
    --grey: #8a888d;
    --grey-strip: #77757a;
    --white: #ffffff;
    --paper: #f7f7f5;
    --ink-soft: #8d8d8d;
  }
  * { box-sizing: border-box; margin: 0; padding: 0; }
  html, body { width: 1200px; height: 886px; overflow: hidden; }
  body {
    background: var(--bg);
    font-family: "Open Sans", Arial, sans-serif;
    position: relative;
  }
  .card {
    position: absolute;
    top: 297px;
    width: 510px;
    height: 291px;
    border-radius: 18px;
    overflow: hidden;
    box-shadow: 0 6px 18px rgba(0,0,0,0.18);
  }
  .card-front { left: 60px; background: var(--paper); }
  .card-back { left: 630px; background: var(--grey); }

  .front-shape { position: absolute; inset: 0; }

  .contact-icons {
    position: absolute;
    left: 0; top: 0;
    width: 40px; height: 100%;
  }

  .contact-block {
    position: absolute;
    left: 60px; top: 30px;
    color: var(--white);
    font-size: 11px;
    line-height: 15px;
    font-weight: 400;
  }
  .contact-name {
    font-size: 19px;
    line-height: 22px;
    font-weight: 400;
    text-transform: uppercase;
    letter-spacing: 0.2px;
  }
  .contact-role {
    font-size: 12px;
    line-height: 16px;
    font-weight: 300;
    text-transform: uppercase;
    margin-bottom: 10px;
  }
  .contact-address { margin-bottom: 8px; }
  .contact-lines { margin-bottom: 0; }

  .brand {
    position: absolute;
    display: flex;
    flex-direction: column;
    align-items: flex-start;
  }
  .brand-row { display: flex; align-items: center; gap: 9px; }
  .brand-dot { border-radius: 50%; flex: none; }
  .brand-name { font-weight: 600; letter-spacing: -0.5px; }
  .brand-tagline {
    font-size: 7px;
    letter-spacing: 1.6px;
    font-weight: 400;
  }

  .brand-front { left: 312px; top: 112px; }
  .brand-front .brand-dot { width: 30px; height: 30px; background: var(--ink-soft); }
  .brand-front .brand-name { font-size: 36px; line-height: 40px; color: var(--green); }
  .brand-front .brand-tagline { color: var(--ink-soft); margin-left: 40px; }

  .brand-back { left: 150px; top: 98px; }
  .brand-back .brand-dot { width: 40px; height: 40px; background: var(--white); }
  .brand-back .brand-name { font-size: 46px; line-height: 52px; color: var(--white); }
  .brand-back .brand-tagline { color: var(--white); margin-left: 50px; font-size: 8px; }

  .back-web {
    position: absolute;
    left: 0; right: 0; bottom: 52px;
    text-align: center;
    color: var(--white);
    font-size: 9px;
    letter-spacing: 5px;
    font-weight: 300;
  }
</style>
</head>
<body>

<div class="card card-front">
  <svg class="front-shape" width="510" height="291" viewBox="0 0 510 291" aria-hidden="true">
    <rect x="0" y="0" width="60" height="291" fill="var(--grey-strip)"/>
    <path d="M40 0 H270 V291 H40 V262 Q40 252 50 246 Q54 244 54 236 V55 Q54 47 50 45 Q40 39 40 29 Z" fill="var(--green)"/>
  </svg>

  <svg class="contact-icons" viewBox="0 0 40 291" aria-hidden="true" fill="var(--white)">
    <!-- person -->
    <circle cx="20" cy="38" r="4"/>
    <path d="M13 50 Q13 43 20 43 Q27 43 27 50 Z"/>
    <!-- pin -->
    <path d="M20 92 C15 92 13 96 13 99 C13 104 20 111 20 111 C20 111 27 104 27 99 C27 96 25 92 20 92 Z"/>
    <circle cx="20" cy="99" r="2.3" fill="var(--grey-strip)"/>
    <!-- phone -->
    <path d="M15 160 Q14 166 19 171 Q24 176 30 175 L30 171 L26 169 L24 171 Q19 169 18 164 L20 162 L18 158 Z" transform="translate(-2,-2)"/>
    <!-- email -->
    <rect x="13" y="193" width="14" height="10" rx="1"/>
    <path d="M13 194 L20 199 L27 194" stroke="var(--grey-strip)" stroke-width="1.2" fill="none"/>
    <!-- globe -->
    <circle cx="20" cy="225" r="7"/>
    <path d="M13 225 H27 M20 218 Q16 225 20 232 M20 218 Q24 225 20 232" stroke="var(--grey-strip)" stroke-width="1" fill="none"/>
  </svg>

  <div class="contact-block">
    <p class="contact-name">Harriet Dunmore</p>
    <p class="contact-role">CEO/Founder</p>
    <p class="contact-address">
      Brackwell House<br>
      Fenmoor Enterprise Park<br>
      Partridge Way<br>
      Norwich<br>
      QB9 3KX
    </p>
    <p class="contact-lines">
      01632 960418<br><br>
      Harriet@plavex.co.uk<br><br>
      www.plavex.co.uk
    </p>
  </div>

  <div class="brand brand-front">
    <div class="brand-row">
      <span class="brand-dot"></span>
      <span class="brand-name">Plavex</span>
    </div>
    <span class="brand-tagline">Technology Recruitment</span>
  </div>
</div>

<div class="card card-back">
  <div class="brand brand-back">
    <div class="brand-row">
      <span class="brand-dot"></span>
      <span class="brand-name">Plavex</span>
    </div>
    <span class="brand-tagline">Technology Recruitment</span>
  </div>
  <p class="back-web">www.plavex.co.uk</p>
</div>

</body>
</html>
```